Book Cover- SNAPSHOTS Coming of Age by Ouray, Colorado: A Quiet High Country Village

Bright Lantern Press Co. is publishing a book
Book Title: SNAPSHOTS Coming of Age by Ouray, Colorado
Subtitle: A Quiet High Country Village
Author: Delia Hartwell
This is a serious of stories and reflections of the author's experiences growing up in small town called Ouray, Colorado.

Front Cover Brief: We would like to have the first picture uploaded below - picture of mountains with fireworks included in the front cover design
Please include
Author Name: Delia Hartwell

Back Cover Brief: The second image of the road included in the back cover design.
Please include the text- by: Delia Hartwell.
Along with this text:

Ouray is miraculous. Being touched by the magic of this beautiful place is my motivation to share the experience.

I was blessed to grow up in a beautiful town and was raised by a loving family during an amazing time of global change. Shared experiences are an exceptional way for us all to learn, grow, and be entertained. I hope you enjoy the stories as much as I enjoyed writing them. After all, the name of Ouray could well be “Magic.”

This book is a collection of memories and shared experiences from growing up with friends and family in A Quiet HIGH Country Village. These recollections were written from a place in my heart where love lives. I loved growing up in Ouray.

SNAPSHOTS Coming Of Age By Ouray, Colorado, is my effort to encourage others to reflect and share their experiences of growing up, wherever that may have been.

If space allows include the name of the publishing company: Bright Lantern Press Co. on back cover

Spine - We also need a spine with the title of the book Coming of Age by Ouray, Colorado : A Quiet HIGH Country Village and Author's name - Delia Hartwell.

```html
<!DOCTYPE html>
<html lang="en">
<head>
<meta charset="utf-8">
<title>SNAPSHOTS Coming of Age by Ouray, Colorado — Book Cover</title>
<link href="https://fonts.googleapis.com/css2?family=Cinzel:wght@400;500&family=Source+Sans+3:wght@400;700&display=swap" rel="stylesheet">
<style>
  :root {
    --sky-deep: #0b5fd0;
    --sky-mid: #2a84e6;
    --sky-light: #5cb2f2;
    --front-top: #0a76e4;
    --front-low: #4d95e2;
    --spine-blue: #3566cf;
    --ink-white: #ffffff;
    --shadow: rgba(10, 30, 80, 0.45);
    --peak-grey: #6d7a96;
    --forest: #23301f;
    --dusk: #3b3f5c;
    --meadow: #6f8f5a;
    --road: #4e5256;
  }
  * { margin: 0; padding: 0; box-sizing: border-box; }
  html, body { width: 1200px; height: 884px; overflow: hidden; background: #fff; }
  .cover-wrap { position: relative; width: 1200px; height: 884px; display: flex; }

  .display { font-family: "Cinzel", serif; color: var(--ink-white); text-shadow: 2px 3px 3px var(--shadow); font-weight: 400; text-align: center; line-height: 1; }

  /* Back cover */
  .back-cover { position: relative; width: 580px; height: 884px; overflow: hidden;
    background: linear-gradient(180deg, var(--sky-deep) 0%, var(--sky-mid) 45%, var(--sky-light) 80%, #8fd0f7 100%); }
  .back-title { position: absolute; top: 88px; left: 0; width: 580px; }
  .back-title .line-main { font-size: 50px; letter-spacing: 1px; }
  .back-title .line-second { font-size: 40px; margin-top: 6px; }
  .back-title .line-place { font-size: 25px; margin-top: 8px; }
  .back-title .line-sub { font-size: 17px; margin-top: 20px; }
  .blurb { position: absolute; top: 300px; left: 68px; width: 458px;
    font-family: "Source Sans 3", sans-serif; font-size: 14.6px; line-height: 18.8px; color: var(--ink-white); }
  .blurb p { text-align: justify; text-align-last: center; margin-bottom: 18.5px; }
  .publisher { position: absolute; top: 658px; left: 0; width: 580px; text-align: center;
    font-family: "Source Sans 3", sans-serif; font-weight: 700; font-size: 17px; color: var(--ink-white); }
  .road-photo { position: absolute; left: 0; bottom: 0; width: 580px; height: 180px;
    background:
      linear-gradient(180deg, rgba(92,178,242,0) 0%, rgba(74,110,130,0.85) 22%, var(--meadow) 55%, #a5b49a 72%, var(--road) 100%); }

  /* Spine */
  .spine { position: relative; width: 41px; height: 884px; background: linear-gradient(180deg, #2d62cc, var(--spine-blue) 60%, #3f74d8); }
  .spine-text { position: absolute; left: 0; width: 41px; writing-mode: vertical-rl; font-family: "Cinzel", serif; color: var(--ink-white); font-size: 14.5px; display: flex; align-items: center; white-space: nowrap; }
  .spine-title { top: 118px; }
  .spine-author { top: 637px; font-size: 16px; letter-spacing: 1px; }

  /* Front cover */
  .front-cover { position: relative; width: 579px; height: 884px; overflow: hidden;
    background: linear-gradient(180deg, var(--front-top) 0%, #2d87e6 30%, var(--front-low) 45%, #6aa3df 60%); }
  .front-photo { position: absolute; left: 0; top: 330px; width: 579px; height: 554px;
    background:
      radial-gradient(ellipse 120px 130px at 330px 160px, rgba(245,170,60,0.85), rgba(245,170,60,0) 100%),
      radial-gradient(ellipse 90px 100px at 430px 200px, rgba(240,190,90,0.6), rgba(240,190,90,0) 100%),
      radial-gradient(ellipse 140px 60px at 250px 330px, rgba(230,160,90,0.45), rgba(230,160,90,0) 100%),
      linear-gradient(180deg, rgba(106,163,223,0) 0%, var(--peak-grey) 18%, var(--dusk) 45%, #4a3d3a 62%, var(--forest) 80%, #1c2a18 100%); }
  .front-sub { position: absolute; top: 72px; left: 0; width: 579px; font-size: 22px; }
  .front-title { position: absolute; top: 128px; left: 0; width: 579px; }
  .front-title .line-main { font-size: 68px; letter-spacing: 1px; }
  .front-title .line-second { font-size: 52px; margin-top: 12px; }
  .front-title .line-place { font-size: 34px; margin-top: 18px; }
  .front-author { position: absolute; top: 768px; left: 0; width: 579px; font-size: 38px; letter-spacing: 2px; }
</style>
</head>
<body>
<main class="cover-wrap">
  <section class="back-cover">
    <div class="back-title display">
      <div class="line-main">SNAPSHOTS</div>
      <div class="line-second">COMING OF AGE</div>
      <div class="line-place">BY OURAY, COLORADO</div>
      <div class="line-sub">A QUIET HIGH COUNTRY VILLAGE</div>
    </div>
    <div class="blurb">
      <p>Ouray is miraculous. Being touched by the magic of this beautiful place is my motivation to share the experience.</p>
      <p>I was blessed to grow up in a beautiful town and was raised by a loving family during an amazing time of global change. Shared experiences are an exceptional way for us all to learn, grow, and be entertained. I hope you enjoy the stories as much as I enjoyed writing them. After all, the name of Ouray could well be “Magic.”</p>
      <p>This book is a collection of memories and shared experiences from growing up with friends and family in a quiet high country village. These recollections were written from a place in my heart where love lives. I loved growing up in Ouray.</p>
      <p>SNAPSHOTS Coming Of Age By Ouray, Colorado, is my effort to encourage others to reflect and share their experiences of growing up, wherever that may have been.</p>
    </div>
    <div class="publisher">BRIGHT LANTERN PRESS CO.</div>
    <div class="road-photo" role="img" aria-label="Photograph of a country road stretching toward mountains with morning fog over green fields"></div>
  </section>

  <section class="spine">
    <div class="spine-text spine-title">SNAPSHOTS COMING OF AGE BY OURAY, COLORADO</div>
    <div class="spine-text spine-author">DELIA HARTWELL</div>
  </section>

  <section class="front-cover">
    <div class="front-photo" role="img" aria-label="Photograph of a mountain valley town at dusk with golden fireworks bursting over the peaks"></div>
    <div class="front-sub display">A QUIET HIGH COUNTRY VILLAGE</div>
    <div class="front-title display">
      <div class="line-main">SNAPSHOTS</div>
      <div class="line-second">COMING OF AGE</div>
      <div class="line-place">BY OURAY, COLORADO</div>
    </div>
    <div class="front-author display">DELIA HARTWELL</div>
  </section>
</main>
</body>
</html>
```